Local Roofing/Construction company business needs new biz card design

We need a new business card design, current cards are from the start of this operation and generic at best. We are a local Construction Company (General Contractor) with a majority of our work originating from insurance claims-exterior finish work is the main focus (Roofs-Siding-Gutters etc). Heavily involved with homeowners and the low ball offers they receive from insurance company's after a insurable event takes place. I have attached some of our original logo file(s) below.

```html
<!DOCTYPE html>
<html lang="en">
<head>
<meta charset="utf-8">
<title>Oakline Construction – Business Card</title>
<link rel="stylesheet" href="https://fonts.googleapis.com/css2?family=Montserrat:wght@400;500;600;700&display=swap">
<style>
  :root {
    --page: #e4e4e4;
    --card: #f6f6f6;
    --ink: #0e1a17;
    --green: #4cb36a;
    --green-deep: #3a9a55;
    --grey-text: #6f6f6f;
    --white: #ffffff;
  }
  * { box-sizing: border-box; margin: 0; padding: 0; }
  html, body { width: 1200px; height: 1200px; overflow: hidden; }
  body {
    background: var(--page);
    font-family: "Montserrat", Arial, sans-serif;
    position: relative;
  }
  .card {
    position: absolute;
    left: 234px;
    width: 730px;
    height: 416px;
    background: var(--card);
    overflow: hidden;
  }
  .card--front { top: 160px; }
  .card--back { top: 632px; }

  .brand {
    position: absolute;
    display: flex;
    align-items: center;
    gap: 14px;
    color: var(--ink);
    font-weight: 700;
    line-height: 1;
  }
  .brand__mark { background: var(--green); flex: none; }
  .brand__name { display: flex; flex-direction: column; gap: 6px; }
  .brand--large { left: 200px; top: 75px; }
  .brand--large .brand__mark { width: 62px; height: 62px; }
  .brand--large .brand__word { font-size: 38px; letter-spacing: 1px; }
  .brand--large .brand__sub { font-size: 19px; letter-spacing: 3px; }
  .brand--small { left: 442px; top: 56px; }
  .brand--small .brand__mark { width: 44px; height: 44px; }
  .brand--small .brand__word { font-size: 27px; letter-spacing: 1px; }
  .brand--small .brand__sub { font-size: 13.5px; letter-spacing: 2px; }

  .specialties { position: absolute; left: 137px; top: 247px; }
  .specialties__title {
    color: var(--green);
    font-weight: 700;
    font-size: 25.5px;
    letter-spacing: 0.3px;
  }
  .specialties__list {
    list-style: none;
    display: grid;
    grid-template-columns: 257px 220px;
    row-gap: 14px;
    margin-top: 22px;
  }
  .specialties__item {
    display: flex; align-items: center; gap: 9px;
    color: var(--grey-text);
    font-size: 19.5px;
  }
  .specialties__icon {
    width: 25px; height: 25px; border-radius: 50%;
    background: var(--green);
    display: flex; align-items: center; justify-content: center;
    flex: none;
  }

  .holder { position: absolute; left: 57px; top: 60px; }
  .holder__name { font-size: 31px; font-weight: 700; color: var(--ink); }
  .holder__name span { color: var(--green); }
  .holder__role { font-size: 19px; color: var(--ink); margin-top: 0; }

  .contact-band {
    position: absolute; left: 0; right: 0; bottom: 0; height: 203px;
    background: linear-gradient(90deg, var(--green-deep), var(--green));
    color: var(--white);
  }
  .contact { position: absolute; left: 55px; top: 30px; font-size: 19px; }
  .contact__address { line-height: 26px; margin-bottom: 8px; }
  .contact__line { display: flex; align-items: center; gap: 10px; height: 28px; }
  .contact__icon { width: 16px; height: 16px; flex: none; }
</style>
</head>
<body>

<section class="card card--front">
  <div class="brand brand--large">
    <div class="brand__mark"></div>
    <div class="brand__name">
      <span class="brand__word">OAKLINE</span>
      <span class="brand__sub">CONSTRUCTION</span>
    </div>
  </div>

  <div class="specialties">
    <h2 class="specialties__title">OUR CONTRACTING SPECIALTIES</h2>
    <ul class="specialties__list">
      <li class="specialties__item">
        <span class="specialties__icon"><svg width="14" height="14" viewBox="0 0 14 14"><path d="M1 7 7 2l6 5M3 6v6h8V6" fill="none" stroke="#fff" stroke-width="1.2"/></svg></span>
        Residential Roofing</li>
      <li class="specialties__item">
        <span class="specialties__icon"><svg width="14" height="14" viewBox="0 0 14 14"><rect x="2" y="2" width="10" height="10" fill="none" stroke="#fff" stroke-width="1.2"/><path d="M5 2v10M9 2v10M2 5h10M2 9h10" stroke="#fff" stroke-width="0.8"/></svg></span>
        Exterior Finishes</li>
      <li class="specialties__item">
        <span class="specialties__icon"><svg width="14" height="14" viewBox="0 0 14 14"><path d="M2 12V5l5-3 5 3v7zM7 2v10" fill="none" stroke="#fff" stroke-width="1.2"/></svg></span>
        Commercial Roofing</li>
      <li class="specialties__item">
        <span class="specialties__icon"><svg width="14" height="14" viewBox="0 0 14 14"><path d="M2 12 7 7l5 5" fill="none" stroke="#fff" stroke-width="1.2"/><circle cx="4" cy="3" r="1" fill="#fff"/><circle cx="7" cy="2.5" r="1" fill="#fff"/><circle cx="10" cy="3" r="1" fill="#fff"/></svg></span>
        Storm Restoration</li>
    </ul>
  </div>
</section>

<section class="card card--back">
  <div class="holder">
    <h1 class="holder__name">Dalton <span>Reyes</span></h1>
    <p class="holder__role">Founder &amp; Director</p>
  </div>

  <div class="brand brand--small">
    <div class="brand__mark"></div>
    <div class="brand__name">
      <span class="brand__word">OAKLINE</span>
      <span class="brand__sub">CONSTRUCTION</span>
    </div>
  </div>

  <div class="contact-band">
    <div class="contact">
      <p class="contact__address">42 Maple Ridge Ct<br>Fairview, MO 63011</p>
      <p class="contact__line">
        <svg class="contact__icon" viewBox="0 0 16 16"><path d="M4 1.5 6.5 5 5 6.5c.8 1.8 2.7 3.7 4.5 4.5L11 9.5l3.5 2.5-1.5 2.5C7.5 14 2 8.5 1.5 3z" fill="var(--ink)"/></svg>
        555-014-2290</p>
      <p class="contact__line">
        <svg class="contact__icon" viewBox="0 0 16 16"><rect x="1" y="3" width="14" height="10" fill="var(--ink)"/><path d="M1 3l7 6 7-6" fill="none" stroke="var(--green)" stroke-width="1.2"/></svg>
        hello@oaklineconstruction.com</p>
      <p class="contact__line">
        <svg class="contact__icon" viewBox="0 0 16 16"><circle cx="8" cy="8" r="7" fill="var(--ink)"/><path d="M1 8h14M8 1c-3 4-3 10 0 14M8 1c3 4 3 10 0 14" fill="none" stroke="var(--green)" stroke-width="1"/></svg>
        oaklineconstruction.com</p>
    </div>
  </div>
</section>

</body>
</html>
```